design a construction company business card

Design business card around our logo. Card must have all the typical info: name, title, address, phone, email, business name, etc. Somewhere on the card I would like to see our motto "Grounded in trust... Driven by dedication." Consider adding a splash of bright orange to the card to complement the blues and silvers/grays in the logo. We are open to metallic inks, textures, etc. We would like to see options on both light and dark backgrounds. The font in the logo is Euro Technic Extended Regular.

```html
<!DOCTYPE html>
<html lang="en">
<head>
<meta charset="utf-8">
<title>Harlow Building, Inc. — Business Card</title>
<link rel="stylesheet" href="https://fonts.googleapis.com/css2?family=Michroma&family=Roboto+Condensed:wght@300;400;700&display=swap">
<style>
  :root {
    --bg: #e9e7e3;
    --white: #ffffff;
    --blue-deep: #23369a;
    --blue-mid: #2b55b8;
    --blue-bright: #1f78c4;
    --silver: #9a9ea6;
    --ink-muted: #6f737b;
    --text-light: #eef3ff;
  }
  * { margin: 0; padding: 0; box-sizing: border-box; }
  html, body { width: 1200px; height: 1040px; overflow: hidden; }
  body {
    background: var(--bg);
    font-family: "Roboto Condensed", "Arial Narrow", sans-serif;
    position: relative;
  }
  .card {
    position: absolute;
    left: 220px;
    width: 760px;
    height: 434px;
    border-radius: 4px;
    overflow: hidden;
    box-shadow: 0 10px 30px rgba(0,0,0,0.18);
  }
  .card--front { top: 66px; background: var(--white); }
  .card--back {
    top: 540px;
    background: radial-gradient(ellipse at 60% 40%, var(--blue-bright) 0%, var(--blue-mid) 45%, var(--blue-deep) 100%);
  }
  .card__shapes { position: absolute; inset: 0; width: 100%; height: 100%; }

  .brand {
    position: absolute;
    font-family: "Michroma", "Eurostile", sans-serif;
    font-weight: 400;
    line-height: 1.15;
    letter-spacing: 1px;
  }
  .card--front .brand {
    top: 58px; right: 150px;
    color: var(--blue-mid);
    font-size: 40px;
    text-align: left;
  }
  .brand__sub { display: block; font-size: 16px; letter-spacing: 3px; }

  .person { position: absolute; left: 56px; top: 210px; }
  .person__name {
    font-family: "Roboto Condensed", "Arial Narrow", sans-serif;
    font-weight: 700;
    color: var(--blue-deep);
    font-size: 28px;
    letter-spacing: 0.5px;
  }
  .person__title {
    color: var(--ink-muted);
    font-size: 17px;
    font-weight: 300;
    letter-spacing: 1px;
    margin-top: 2px;
  }

  .contact {
    position: absolute;
    left: 56px; bottom: 34px;
    list-style: none;
    color: var(--text-light);
    font-size: 17px;
    font-weight: 300;
  }
  .contact li { display: flex; align-items: center; gap: 10px; line-height: 27px; }
  .contact svg { width: 14px; height: 14px; fill: var(--text-light); flex: none; }

  .address {
    position: absolute;
    right: 40px; top: 230px;
    color: var(--text-light);
    font-size: 17px;
    font-weight: 300;
    text-align: right;
    line-height: 25px;
    font-style: normal;
  }

  .card--back .brand {
    left: 50px; bottom: 92px;
    color: var(--white);
    font-size: 54px;
  }
  .card--back .brand__sub { font-size: 20px; letter-spacing: 4px; }
  .motto {
    position: absolute;
    left: 52px; bottom: 50px;
    color: var(--white);
    font-size: 18px;
    font-weight: 300;
    letter-spacing: 0.5px;
  }
</style>
</head>
<body>

<section class="card card--front" aria-label="Business card front">
  <svg class="card__shapes" viewBox="0 0 760 434" preserveAspectRatio="none" aria-hidden="true">
    <defs>
      <linearGradient id="band" x1="0" y1="1" x2="1" y2="0">
        <stop offset="0" stop-color="#23369a"/>
        <stop offset="0.5" stop-color="#1f78c4"/>
        <stop offset="1" stop-color="#23369a"/>
      </linearGradient>
    </defs>
    <polygon points="418,194 760,194 760,180 430,180" fill="#9a9ea6"/>
    <polygon points="0,288 330,288 404,206 760,206 760,434 0,434" fill="url(#band)"/>
  </svg>

  <div class="brand">HARLOW<span class="brand__sub">BUILDING, INC.</span></div>

  <div class="person">
    <p class="person__name">DANIEL REYES</p>
    <p class="person__title">CEO/FOUNDER</p>
  </div>

  <ul class="contact">
    <li><svg viewBox="0 0 16 16"><path d="M3 1l3 3-2 2c1 2 3 4 5 5l2-2 3 3-2 3C6 15 1 10 0 4z"/></svg>555 201 4870</li>
    <li><svg viewBox="0 0 16 16"><path d="M1 3h14v10H1z M1 3l7 6 7-6" fill="none" stroke="#eef3ff" stroke-width="1.6"/></svg>hello@harlowbuild.com</li>
    <li><svg viewBox="0 0 16 16"><circle cx="8" cy="8" r="7"/></svg>www.harlowbuild.com</li>
  </ul>

  <address class="address">412 Spruce Hollow Road<br>Fairbanks, Alaska 99701</address>
</section>

<section class="card card--back" aria-label="Business card back">
  <svg class="card__shapes" viewBox="0 0 760 434" preserveAspectRatio="none" aria-hidden="true">
    <polygon points="0,150 90,40 330,40 300,70 60,70 0,140" fill="#ffffff" opacity="0.07"/>
    <polygon points="0,215 130,95 470,95 430,140 140,140 0,260" fill="#ffffff" opacity="0.06"/>
    <polygon points="0,300 190,170 300,170 250,210 120,210 0,300" fill="#ffffff" opacity="0.05"/>
  </svg>
  <div class="brand">HARLOW<span class="brand__sub">BUILDING, INC.</span></div>
  <p class="motto">Grounded in trust... Driven by dedication.</p>
</section>

</body>
</html>
```